Tolvik Commercial Cleaning is lookong for a new business card design.

A fresh new design that's professional and stylish. We need a serious upgrade to our business cards. I have included pictures of our existing ones. Our clients include professional individuals and business owners. We woupdblike something professional and upbeat. Please have fun and see what you come uo with.

Target Market(s)

Property managers, business owners, facility managers and other similar professionals

Industry/Entity Type

Janitorial

Contact Information for Business Card

Name, cell, office number, email, web address

Font styles to use
Sans Serif

Colors

Designer to choose colors to be used in the design.

Requirements
Must have
• please use the green color in our logo
Nice to have
• Bar code
Should not have
• Address

```html
<!DOCTYPE html>
<html lang="en">
<head>
<meta charset="utf-8">
<title>Tolvik Commercial Cleaning – Business Card</title>
<link href="https://fonts.googleapis.com/css2?family=Montserrat:wght@700&family=Open+Sans:wght@400&display=swap" rel="stylesheet">
<style>
  :root {
    --backdrop: #232323;
    --card-cream: #fdfdf2;
    --brand-green: #3ab65a;
    --brand-blue: #4274ad;
    --ink: #1e1e1e;
    --rule: #2a2a2a;
  }
  * { margin: 0; padding: 0; box-sizing: border-box; }
  html, body { width: 1200px; height: 780px; overflow: hidden; }
  body {
    background: var(--backdrop);
    font-family: "Open Sans", Arial, sans-serif;
    position: relative;
  }
  .card {
    position: absolute;
    top: 236px;
    width: 540px;
    height: 308px;
    border-radius: 22px;
    background: var(--card-cream);
    overflow: hidden;
    box-shadow: 0 10px 24px rgba(0,0,0,.55);
  }
  .card--front { left: 40px; }
  .card--back { left: 620px; }

  .front-band {
    position: absolute;
    left: 0; right: 0;
    top: 42px; bottom: 42px;
    background: var(--brand-green);
    display: flex;
    align-items: center;
    justify-content: center;
  }
  .wordmark {
    font-family: "Montserrat", Arial, sans-serif;
    font-weight: 700;
    display: flex;
    align-items: center;
    gap: 14px;
    letter-spacing: .5px;
  }
  .wordmark__dot {
    width: 22px; height: 22px;
    border-radius: 50%;
  }
  .front-band .wordmark { font-size: 64px; color: #2f8f45; }
  .front-band .wordmark__dot { background: #2f8f45; }

  .back-brand {
    position: absolute;
    left: 40px; top: 0; width: 230px; height: 250px;
    display: flex; align-items: center; justify-content: center;
  }
  .back-brand .wordmark { font-size: 50px; color: var(--brand-green); }
  .back-brand .wordmark__dot { background: var(--brand-green); width: 18px; height: 18px; }

  .divider {
    position: absolute;
    left: 282px; top: 70px;
    width: 1px; height: 120px;
    background: var(--rule);
  }
  .contact {
    position: absolute;
    left: 306px; top: 82px;
  }
  .contact__name {
    font-family: "Montserrat", Arial, sans-serif;
    font-weight: 700;
    font-size: 23px;
    line-height: 1.1;
    margin-bottom: 14px;
    white-space: nowrap;
  }
  .contact__first { color: var(--brand-green); }
  .contact__last { color: var(--brand-blue); }
  .contact__list { list-style: none; }
  .contact__item {
    display: flex; align-items: center; gap: 8px;
    font-size: 12.5px; color: var(--ink);
    line-height: 20px;
  }
  .contact__icon { width: 12px; height: 12px; flex: none; }
  .stripes {
    position: absolute; left: 0; bottom: 0;
    width: 540px; height: 60px;
  }
</style>
</head>
<body>
  <section class="card card--front" aria-label="Business card front">
    <div class="front-band">
      <div class="wordmark"><span class="wordmark__dot"></span>Tolvik</div>
    </div>
  </section>

  <section class="card card--back" aria-label="Business card back">
    <div class="back-brand">
      <div class="wordmark"><span class="wordmark__dot"></span>Tolvik</div>
    </div>
    <div class="divider"></div>
    <div class="contact">
      <p class="contact__name"><span class="contact__first">Mara</span> <span class="contact__last">Fenwick</span></p>
      <ul class="contact__list">
        <li class="contact__item">
          <svg class="contact__icon" viewBox="0 0 24 24"><path fill="var(--brand-green)" d="M6.6 10.8a15 15 0 0 0 6.6 6.6l2.2-2.2c.3-.3.7-.4 1-.2 1.1.4 2.3.6 3.6.6.6 0 1 .4 1 1V20c0 .6-.4 1-1 1A17 17 0 0 1 3 4c0-.6.4-1 1-1h3.5c.6 0 1 .4 1 1 0 1.2.2 2.4.6 3.6.1.3 0 .7-.2 1z"/></svg>
          (555) 014-2290
        </li>
        <li class="contact__item">
          <svg class="contact__icon" viewBox="0 0 24 24"><path fill="var(--brand-green)" d="M2 5h20v14H2z"/><path fill="none" stroke="var(--card-cream)" stroke-width="2" d="M3 6l9 7 9-7"/></svg>
          mara@tolvikcleaning.com
        </li>
        <li class="contact__item">
          <svg class="contact__icon" viewBox="0 0 24 24"><circle cx="12" cy="12" r="10" fill="var(--brand-green)"/><path fill="none" stroke="var(--card-cream)" stroke-width="1.5" d="M2 12h20M12 2c3 3 3 17 0 20M12 2c-3 3-3 17 0 20"/></svg>
          www.tolvikcleaning.com
        </li>
      </ul>
    </div>
    <svg class="stripes" viewBox="0 0 540 60" aria-hidden="true">
      <polygon points="0,44 330,44 352,60 0,60" fill="var(--brand-green)"/>
      <polygon points="330,44 540,0 540,60 352,60" fill="var(--brand-blue)"/>
      <polygon points="330,44 352,44 370,60 352,60" fill="var(--card-cream)"/>
    </svg>
  </section>
</body>
</html>
```